Brackwell Yard Services Flyer Design

I need a new flyer design for my business, Brackwell Yard Services. I’ll be providing my old flyer and logo as references. The new flyer should feature updated wording, contact information, logos, and photos, but still keep the original “What We Do” section and include the phrase “Don’t See? Just Ask!” somewhere near the services. The flyer needs to look great in black and white for door-to-door handouts but also be eye-catching and professional enough for social media use.

The updated content should include the headline “Transforming Outdoor Spaces with Hard Work & Precision” and highlight three main service areas: Landscaping Services (project-based landscaping to clean, prepare, and transform outdoor spaces with precision), Property Cleanup (quick hauls, debris removal, or full cleanouts—no job too big or small), and Ground Preparation (pad preparation, brush removal, and fire lines—making properties safe, functional, and project-ready).

Please also include a “Why Choose Us?” section that lists: Locally owned since 2022, Reliable & affordable – no corners cut, Professional results you can trust, LICENSED AND Insured, and Quality work / on time / references / flexible / follow-up.

At the bottom, include the contact details: Call or Text Today!
www.brackwellyard.example
| sales@brackwellyard.example
| (555) 014-7293

The overall design should be clean, professional, and easy to read with a layout that clearly shows what we offer. Use visuals that represent outdoor services, landscaping, and property cleanup/prep work. I want something that feels trustworthy, family-friendly, and modern.
Use the same photo of leaf clean up from the original flyer if possible.
Our company colors are also black and white. For the most part.

```html
<!DOCTYPE html>
<html lang="en">
<head>
<meta charset="utf-8">
<title>Brackwell Yard Services Flyer</title>
<link href="https://fonts.googleapis.com/css2?family=Krona+One&family=Exo+2:ital,wght@1,800;1,900&family=Roboto+Condensed:wght@400;500&family=Open+Sans:wght@600&display=swap" rel="stylesheet">
<style>
:root{
  --ink:#000;
  --paper:#fff;
  --mat:#9b9b9b;
  --panel:#d9d9d9;
  --panel-line:#c4c4c4;
  --muted:#9a9a9a;
  --hero-dark:#1e1f22;
}
*{margin:0;padding:0;box-sizing:border-box}
html,body{width:900px;height:1200px;overflow:hidden;background:var(--mat)}
.flyer{position:absolute;left:32px;top:0;width:836px;height:1200px;background:var(--paper);overflow:hidden;font-family:"Roboto Condensed",sans-serif;color:var(--ink)}
.abs{position:absolute}
.hero{left:0;top:0;width:836px;height:474px;background:linear-gradient(135deg,#3a3a36 0%,#26282b 45%,#1a1c22 100%)}
.hero-photo{left:20px;top:15px}
.brand{left:456px;top:40px;width:340px;font-family:"Krona One",sans-serif;font-size:26px;color:var(--paper);line-height:1.25;display:flex;align-items:center;gap:12px}
.brand-mark{width:30px;height:30px;background:var(--paper);flex:none}
.headline{left:456px;top:144px;font-family:"Krona One",sans-serif;color:var(--paper);line-height:1}
.headline span{display:block;white-space:nowrap}
.hl-sm{font-size:26px;margin-bottom:15px}
.hl-lg{font-size:44px;margin-bottom:14px}
.hl-md{font-size:31px;margin-bottom:15px}
.hero-rule{left:658px;top:392px;width:137px;height:2px;background:var(--paper)}
.side-panel{left:626px;top:474px;width:210px;height:664px;background:var(--panel)}
.why{left:0;top:491px;width:366px;height:200px;background:var(--panel);border-radius:0 14px 14px 0}
.heading{font-family:"Exo 2",sans-serif;font-style:italic;font-weight:900;font-size:31px;line-height:1}
.why .heading{position:absolute;left:34px;top:12px}
.why-list{position:absolute;left:34px;top:52px;list-style:none;font-size:17.5px;line-height:23.3px}
.why-list li{position:relative;padding-left:25px}
.why-list li::before{content:"";position:absolute;left:3px;top:7px;width:9px;height:9px;background:var(--ink);transform:rotate(45deg)}
.what-title{left:34px;top:715px}
.what-rule{left:224px;top:730px;width:126px;height:2px;background:var(--panel-line)}
.pill{height:25px;background:var(--ink);color:var(--paper);font-family:"Open Sans",sans-serif;font-weight:600;font-size:18px;line-height:25px}
.pill-remove{left:0;top:768px;width:139px;border-radius:0 13px 13px 0;padding-left:36px}
.pill-install{left:235px;top:768px;width:116px;border-radius:13px;text-align:center}
.pill-maint{left:0;top:910px;width:351px;border-radius:0 13px 13px 0;padding-left:36px}
.svc-list{list-style:none;font-size:17px;line-height:23.4px}
.svc-list li{position:relative;padding-left:24px}
.svc-list li::before{content:"";position:absolute;left:2px;top:8px;width:9px;height:9px;background:var(--muted);transform:rotate(45deg)}
.list-remove{left:37px;top:801px}
.list-install{left:257px;top:801px}
.list-maint{left:37px;top:944px}
.ask{left:18px;top:1050px;font-family:"Exo 2",sans-serif;font-weight:900;font-size:35px;font-style:normal;letter-spacing:-.2px}
.contact{left:0;top:1105px;width:382px;height:95px;background:var(--panel);border-radius:0 70px 0 0}
.contact-lead{position:absolute;left:19px;top:9px;font-size:13.5px;font-weight:500;display:flex;align-items:center;width:355px;gap:6px}
.contact-lead i{flex:1;border-top:1px dashed var(--muted);margin-top:2px}
.contact-row{position:absolute;left:54px;display:flex;align-items:center;gap:10px;font-size:21px;font-weight:500}
.row-web{top:28px}
.row-mail{top:54px}
.callbar{left:381px;top:1138px;width:455px;height:62px;background:var(--ink)}
.callbar svg{position:absolute;left:73px;top:6px}
.phone{position:absolute;left:142px;top:13px;font-family:"Krona One",sans-serif;font-size:27px;color:var(--paper);white-space:nowrap}
.card{left:382px;width:419px;height:208px;background:var(--paper);border:2px solid var(--panel-line);border-radius:12px;box-shadow:0 0 0 2px var(--paper) inset}
.card-photo{position:absolute;left:3px;top:3px;width:241px;height:200px;border-radius:9px 0 0 9px}
.card-head{position:absolute;left:244px;top:3px;width:171px;height:79px;background:var(--ink);border-radius:0 9px 0 0;color:var(--paper);font-family:"Exo 2",sans-serif;font-style:italic;font-weight:800;font-size:18px;line-height:22px;padding:17px 0 0 15px;text-transform:uppercase}
.card-body{position:absolute;left:262px;top:94px;width:150px;font-size:14.5px;font-weight:500;line-height:17.5px;padding-left:19px}
.card-body svg{position:absolute;left:0;top:2px}
.card-1{top:487px}
.card-2{top:704px}
.card-3{top:920px}
.photo-patio{background:linear-gradient(160deg,#9ab08e 0%,#c9c2c4 55%,#b6a7a2 100%)}
.photo-debris{background:linear-gradient(160deg,#a9927a 0%,#7f7a6f 50%,#8c9c94 100%)}
.photo-prep{background:linear-gradient(180deg,#c4d3e6 0%,#a7a9ab 45%,#b7ab95 100%)}
</style>
</head>
<body>
<div class="flyer">

  <section class="abs hero" role="img" aria-label="Dark photo of a trailer loaded with hauled junk and debris"></section>

  <svg class="abs hero-photo" width="394" height="434" viewBox="0 0 394 434">
    <defs>
      <linearGradient id="patioYard" x1="0" y1="0" x2="0" y2="1">
        <stop offset="0" stop-color="#c9d6e4"/>
        <stop offset="0.35" stop-color="#6f8a5a"/>
        <stop offset="0.6" stop-color="#a39686"/>
        <stop offset="1" stop-color="#cdb596"/>
      </linearGradient>
    </defs>
    <path d="M197 6 Q207 2 217 8 L368 96 Q384 105 384 124 L384 312 Q384 330 368 339 L217 427 Q207 432 197 427 L28 339 Q12 330 12 312 L12 124 Q12 105 28 96 L177 8 Q187 2 197 6 Z" fill="#fff"/>
    <path d="M197 13 Q206 9 214 14 L362 100 Q377 109 377 125 L377 311 Q377 327 362 335 L214 421 Q206 425 197 421 L33 335 Q19 327 19 311 L19 125 Q19 109 33 100 L180 14 Q188 9 197 13 Z" fill="url(#patioYard)" role="img" aria-label="Photo of a finished backyard with a stone retaining wall, gravel bed, patio and wooden fence"/>
  </svg>

  <div class="abs brand"><span class="brand-mark"></span><span>BRACKWELL YARD SERVICES</span></div>

  <h1 class="abs headline">
    <span class="hl-sm">TRANSFORMING</span>
    <span class="hl-lg">OUTDOOR</span>
    <span class="hl-md">SPACES WITH</span>
    <span class="hl-md">HARD WORK</span>
    <span class="hl-md">&amp; PRECISION</span>
  </h1>
  <div class="abs hero-rule"></div>

  <div class="abs side-panel"></div>

  <section class="abs why">
    <h2 class="heading">Why Choose Us?</h2>
    <ul class="why-list">
      <li>Locally owned since 2022</li>
      <li>Reliable &amp; affordable – no corners cut</li>
      <li>Professional results you can trust</li>
      <li>Licensed And Insured</li>
      <li>Quality work / on time / references /<br>flexible / follow-up</li>
    </ul>
  </section>

  <h2 class="abs heading what-title">What We Do</h2>
  <div class="abs what-rule"></div>

  <div class="abs pill pill-remove">REMOVE</div>
  <div class="abs pill pill-install">INSTALL</div>
  <ul class="abs svc-list list-remove">
    <li>Junk removal</li>
    <li>Trash &amp; waste hauling</li>
    <li>Yard and garden cleanup</li>
    <li>Appliance removal</li>
  </ul>
  <ul class="abs svc-list list-install">
    <li>Mulch</li>
    <li>D.G.</li>
    <li>Plants</li>
    <li>Rock</li>
  </ul>

  <div class="abs pill pill-maint">MAINTENANCE &amp; OTHER</div>
  <ul class="abs svc-list list-maint">
    <li>Yard clean up</li>
    <li>Weed prevention (pre-emergent)</li>
    <li>Roof &amp; gutter cleaning</li>
    <li>Fence &amp; deck staining</li>
  </ul>

  <p class="abs ask">Don’t See? Just Ask!</p>

  <section class="abs card card-1">
    <div class="card-photo photo-patio" role="img" aria-label="Photo of a new paver patio laid beside a house"></div>
    <h3 class="card-head">Landscaping<br>Services</h3>
    <p class="card-body"><svg width="13" height="13" viewBox="0 0 13 13"><circle cx="6.5" cy="6.5" r="6.5"/><path d="M3.5 6.7l2 2 4-4.2" stroke="#fff" stroke-width="1.6" fill="none"/></svg>Project-based landscaping to Clean Prepare, and Transform Outdoor Spaces with precision</p>
  </section>

  <section class="abs card card-2">
    <div class="card-photo photo-debris" role="img" aria-label="Photo of a trailer piled with old carpet, furniture and debris from a cleanup"></div>
    <h3 class="card-head">Property<br>Cleanup</h3>
    <p class="card-body"><svg width="13" height="13" viewBox="0 0 13 13"><circle cx="6.5" cy="6.5" r="6.5"/><path d="M3.5 6.7l2 2 4-4.2" stroke="#fff" stroke-width="1.6" fill="none"/></svg>Quick hauls, Debris Removal, or full cleanouts—no job too big or small</p>
  </section>

  <section class="abs card card-3">
    <div class="card-photo photo-prep" role="img" aria-label="Photo of a graded dirt pad with stacked pavers and a compactor ready for installation"></div>
    <h3 class="card-head">Ground<br>Preparation</h3>
    <p class="card-body"><svg width="13" height="13" viewBox="0 0 13 13"><circle cx="6.5" cy="6.5" r="6.5"/><path d="M3.5 6.7l2 2 4-4.2" stroke="#fff" stroke-width="1.6" fill="none"/></svg>Pad preparation, Brush removal, and Fire lines—making properties safe, Functional, and Project-Ready</p>
  </section>

  <section class="abs contact">
    <p class="contact-lead">Call or Text Today! <i></i></p>
    <p class="contact-row row-web">
      <svg width="17" height="17" viewBox="0 0 18 18" fill="none" stroke="#000" stroke-width="1.5"><circle cx="9" cy="9" r="7.5"/><ellipse cx="9" cy="9" rx="3.3" ry="7.5"/><path d="M1.5 9h15M3 5h12M3 13h12"/></svg>
      www.brackwellyard.example
    </p>
    <p class="contact-row row-mail">
      <svg width="17" height="13" viewBox="0 0 18 13"><rect width="18" height="13" fill="#000"/><path d="M1 1l8 6 8-6" stroke="#d9d9d9" stroke-width="1.4" fill="none"/></svg>
      sales@brackwellyard.example
    </p>
  </section>

  <section class="abs callbar">
    <svg width="50" height="50" viewBox="0 0 50 50" fill="none" stroke="#fff">
      <circle cx="25" cy="25" r="23.5" stroke-width="1.8"/>
      <path d="M18 15.5l4 4.5-2.3 3a14 14 0 0 0 7.3 7.3l3-2.3 4.5 4-2.4 3.4c-8.5-.3-16-7.8-16.5-16.5z" fill="#fff" stroke="none"/>
      <path d="M27 15a8 8 0 0 1 8 8M27 19.5a3.6 3.6 0 0 1 3.5 3.5" stroke-width="1.8"/>
    </svg>
    <p class="phone">(555) 014-7293</p>
  </section>

</div>
</body>
</html>
```